My Web Development Portfolio site

I'm a web developer and I need a web design that can showcase my web development portfolio. I like most of the websites from this link: http://www.lumivexa.com/portfolios/examples-503917. My ideal design should be modern, clean and fun. I will let the designer decided the color theme for the website.

Target Market(s)

Potential Employers.

Number of Pages Required

1 page

Requirements
Must have
• - Menu bar that includes at least: About Me, Blog, Contact, Project/Work
• - Excellent color theme
• - Use the logo I provided (see attachment)
Nice to have
• - Some animation
• - Fun yet modern design

```html
<!DOCTYPE html>
<html lang="en">
<head>
<meta charset="utf-8">
<title>codevanta — Web Developer Portfolio</title>
<link href="https://fonts.googleapis.com/css2?family=Lato:wght@400;700&family=Roboto+Condensed:wght@700&display=swap" rel="stylesheet">
<style>
:root{
  --orange:#f58a4b;
  --orange-dark:#ee7a35;
  --ink:#1f1f1f;
  --text:#333;
  --muted:#666;
  --rule:#cfcfcf;
  --panel:#f1f1f2;
  --white:#fff;
  --navy:#1c3a63;
}
*{box-sizing:border-box;margin:0;padding:0}
html,body{width:773px;height:1200px;overflow:hidden;background:var(--white);font-family:'Lato',sans-serif;color:var(--text)}
.page{position:relative;width:773px;height:1200px}
.abs{position:absolute}

/* Sidebar */
.sidebar{left:0;top:0;width:205px;height:1045px;background:var(--white);border-right:2px solid var(--orange)}
.brand{left:0;top:22px;width:205px;text-align:center}
.brand-dot{display:block;width:30px;height:30px;border-radius:50%;background:var(--orange);margin:0 auto 8px}
.brand-name{font-size:24px;font-weight:400;color:var(--orange);letter-spacing:1px}
.nav{left:26px;top:93px;width:157px;list-style:none}
.nav li{height:33px;display:flex;align-items:center;justify-content:space-between;padding:0 10px;border-bottom:1px solid #e6e6e6;font-size:10.5px;font-weight:700;color:var(--ink);margin-bottom:0}
.nav li.active{background:var(--orange);color:var(--white);height:25px;border:none;margin-bottom:4px}
.nav svg{width:15px;height:15px}
.follow{left:35px;top:264px;width:150px;display:flex;align-items:center;gap:4px;font-size:10.5px;font-weight:700;color:var(--ink)}
.follow span{margin-right:14px}
.social{width:19px;height:19px;border-radius:50%;background:var(--navy)}
.social.alt{background:var(--orange-dark)}
.section-title{font-size:17px;font-weight:700;color:var(--ink)}
.section-title em{font-style:normal;font-weight:400;color:var(--orange)}
.about-title{left:26px;top:309px}
.about-rule{left:26px;top:339px;width:158px;height:1px;background:#999}
.avatar{left:46px;top:362px;width:121px;height:121px;border-radius:50%;border:3px solid var(--orange);background:radial-gradient(circle at 50% 40%,#c9a48c,#8c7466 60%,#5a5f66)}
.person{left:27px;top:495px;font-family:'Roboto Condensed',sans-serif;font-size:14px;color:var(--ink)}
.role{left:27px;top:518px;font-size:9px;font-weight:700;color:var(--ink)}
.bio{left:27px;top:540px;width:158px;font-size:9.4px;line-height:14.9px;color:#444}
.read-more{left:27px;top:757px;font-size:8px;color:var(--ink);text-decoration:underline}

/* Hero */
.hero{left:207px;top:0;width:566px;height:296px;background:radial-gradient(ellipse at 75% 45%,#7a5a2e 0%,#2f2a2a 35%,#121417 75%)}
.hero-caption{left:207px;top:258px;width:566px;text-align:center;font-size:17.5px;font-weight:700;color:var(--white)}

/* Portfolio */
.portfolio{left:207px;top:296px;width:566px;height:749px;background:linear-gradient(160deg,#f5f5f6,#ececee)}
.work-title{left:229px;top:307px;font-size:18px}
.work-rule{left:229px;top:339px;width:519px;height:1px;background:#999}
.arrow-btn{width:16px;height:16px;border-radius:50%;border:1px solid #aaa;background:var(--white);display:flex;align-items:center;justify-content:center}
.arrow-btn svg{width:7px;height:7px}
.card{background:var(--white);padding:6px;box-shadow:0 2px 5px rgba(0,0,0,.08)}
.thumb{width:100%;height:100%}
.overlay{left:6px;top:6px;right:6px;bottom:6px;background:rgba(110,110,120,.55);display:flex;align-items:center;justify-content:center;gap:6px}
.chip{height:16px;padding:0 6px;display:flex;align-items:center;gap:3px;font-size:8px;font-weight:700;background:var(--white);color:var(--ink)}
.chip.demo{background:var(--orange);color:var(--white)}
.chip svg{width:9px;height:9px}
.pager{left:387px;top:1005px;display:flex;gap:8px;align-items:center;font-size:9.5px}
.pg{height:17px;display:flex;align-items:center;justify-content:center;border:1px solid var(--orange);background:var(--white);color:var(--ink);padding:0 6px;gap:4px}
.pg.num{width:17px;padding:0;border:none;background:#cfcfcf}
.pg.num.on{background:var(--orange);color:var(--white)}
.pg svg{width:7px;height:7px}

/* Contact */
.contact-title{left:230px;top:1066px;font-size:18px}
.contact-rule{left:230px;top:1095px;width:518px;height:1px;background:#999}
.info{top:1115px;display:flex;gap:10px;font-size:9.5px;line-height:14px;color:var(--ink)}
.info svg{width:22px;height:24px;flex:none}
.footer{left:0;top:1172px;width:773px;height:28px;background:var(--orange);color:var(--white);font-size:8px;text-align:center;line-height:28px}
</style>
</head>
<body>
<div class="page">

  <aside class="abs sidebar"></aside>
  <div class="abs brand"><span class="brand-dot"></span><span class="brand-name">codevanta</span></div>

  <ul class="abs nav">
    <li class="active">Home
      <svg viewBox="0 0 16 16" fill="#fff"><path d="M8 1 0.5 8h2v7h4v-4h3v4h4V8h2z"/></svg></li>
    <li>About Me
      <svg viewBox="0 0 16 16" fill="var(--orange)"><circle cx="9" cy="3" r="1.6"/><path d="M6 6h4l-2 8H6z"/></svg></li>
    <li>Latest Blog
      <svg viewBox="0 0 16 16" fill="none" stroke="var(--orange)" stroke-width="1.6"><circle cx="4" cy="12" r="1.4" fill="var(--orange)"/><path d="M3 7a6 6 0 0 1 6 6M3 3a10 10 0 0 1 10 10"/></svg></li>
    <li>Our Projects
      <svg viewBox="0 0 16 16" fill="none" stroke="var(--orange)" stroke-width="1.4"><rect x="1" y="3" width="14" height="9"/><path d="M5 15h6M8 12v3"/></svg></li>
    <li>Contact Us
      <svg viewBox="0 0 16 16" fill="var(--orange)"><path d="M3 2l3 3-2 2c1 2 3 4 5 5l2-2 3 3-2 2C7 15 1 9 1 4z"/></svg></li>
  </ul>

  <div class="abs follow"><span>Follow Us</span>
    <i class="social" aria-label="Social profile"></i>
    <i class="social" aria-label="Social profile"></i>
    <i class="social" aria-label="Social profile"></i>
    <i class="social alt" aria-label="Social profile"></i>
  </div>

  <h2 class="abs section-title about-title">About <em>Me</em></h2>
  <div class="abs about-rule"></div>
  <div class="abs avatar" role="img" aria-label="Portrait photo of the developer"></div>
  <div class="abs person">Marlo Venner</div>
  <div class="abs role">I Am A Web Developer By Profession</div>
  <p class="abs bio">Lorem ipsum dolor sit amet, erererwe eerereer consectetuer adipiscing elit, sed diam nonummy nibh euismod wer tincidunt ut laoreet dolore magnaerrr aliquam erat volutpat. Ut wisi enim ad minim veniam, quis nostrud exerciwe tation ullamcorper suscipit lobortiser nisl ut aliquip ex ea commodo erwerr consequat. Duis autem vel eum iriure dolor in hendrerit in vulputate veliert esse molestie consequat, vel illumere dolore eu feugiat nulla facilisis atewri vero eros et accumsan et iusto odioei dignissim qui blandit praesent.</p>
  <a class="abs read-more">Read More +</a>

  <div class="abs hero" role="img" aria-label="Businessman's open hand with glowing floating screenshots of websites"></div>
  <div class="abs hero-caption">Lorem ipsum dolor sit amet, ectetuer adipiscing elit...</div>

  <section class="abs portfolio"></section>
  <h2 class="abs section-title work-title">Web <em>Portfolio</em></h2>
  <div class="abs arrow-btn" style="left:709px;top:312px"><svg viewBox="0 0 8 8" fill="none" stroke="#666"><path d="M5 1 2 4l3 3"/></svg></div>
  <div class="abs arrow-btn" style="left:731px;top:312px"><svg viewBox="0 0 8 8" fill="none" stroke="#666"><path d="M3 1l3 3-3 3"/></svg></div>
  <div class="abs work-rule"></div>

  <div class="abs card" style="left:230px;top:361px;width:244px;height:152px"><div class="thumb" role="img" aria-label="Bakery website screenshot with cookies" style="background:linear-gradient(160deg,#6a2a14,#3b1609)"></div></div>
  <div class="abs card" style="left:503px;top:361px;width:244px;height:152px"><div class="thumb" role="img" aria-label="Tile showroom website screenshot with living room" style="background:linear-gradient(180deg,#1b1b1b,#4a3a33 60%,#222)"></div></div>

  <div class="abs card" style="left:229px;top:535px;width:165px;height:257px"><div class="thumb" role="img" aria-label="Musician website screenshot" style="background:linear-gradient(180deg,#e8eef3 0%,#3a8bb5 30%,#1f5f80 70%,#111 100%)"></div></div>
  <div class="abs card" style="left:406px;top:535px;width:164px;height:257px"><div class="thumb" role="img" aria-label="Personal website screenshot with desk items" style="background:linear-gradient(180deg,#d9d6d2,#bdb8b2)"></div>
    <div class="abs overlay">
      <span class="chip"><svg viewBox="0 0 10 10" fill="none" stroke="#333" stroke-width="1.2"><circle cx="4" cy="4" r="3"/><path d="M6.3 6.3 9 9"/></svg>Zoom In</span>
      <span class="chip demo"><svg viewBox="0 0 10 10" fill="none" stroke="#fff" stroke-width="1.4"><path d="M8 3A3.5 3.5 0 1 0 8.5 6"/></svg>Live Demo</span>
    </div>
  </div>
  <div class="abs card" style="left:583px;top:535px;width:165px;height:257px"><div class="thumb" role="img" aria-label="Company website screenshot with team photo" style="background:linear-gradient(180deg,#5cc6cf 0%,#5cc6cf 30%,#f7f7f7 31%,#eee 100%)"></div></div>

  <div class="abs card" style="left:230px;top:812px;width:244px;height:155px"><div class="thumb" role="img" aria-label="Mexican restaurant website screenshot" style="background:linear-gradient(180deg,#f7b21b,#e9651a 60%,#1e7f8a)"></div></div>
  <div class="abs card" style="left:503px;top:812px;width:244px;height:155px"><div class="thumb" role="img" aria-label="Cosmetics shop website screenshot with baby products" style="background:linear-gradient(160deg,#c21f6a,#8a1448)"></div></div>

  <nav class="abs pager">
    <span class="pg"><svg viewBox="0 0 8 8" fill="none" stroke="#333"><path d="M5 1 2 4l3 3"/></svg>Previous</span>
    <span class="pg num" style="margin-left:6px">1</span>
    <span class="pg num on">2</span>
    <span class="pg num">3</span>
    <span class="pg" style="margin-left:12px">Next<svg viewBox="0 0 8 8" fill="none" stroke="#333"><path d="M3 1l3 3-3 3"/></svg></span>
  </nav>

  <h2 class="abs section-title contact-title">Contact <em>Information</em></h2>
  <div class="abs contact-rule"></div>
  <div class="abs info" style="left:229px">
    <svg viewBox="0 0 22 24"><path d="M11 1a8 8 0 0 0-8 8c0 6 8 14 8 14s8-8 8-14a8 8 0 0 0-8-8z" fill="var(--orange)"/><circle cx="11" cy="9" r="3" fill="#fff"/></svg>
    <div>123, Lorem ipsum dolor sit amet,<br>consectetuer adipiscing</div>
  </div>
  <div class="abs info" style="left:428px">
    <svg viewBox="0 0 22 24" fill="var(--orange)"><path d="M4 2l5 5-3 3c2 3 4 5 7 7l3-3 5 5-3 3C10 22 1 13 2 5z"/></svg>
    <div>Phone<br>123-456-7890</div>
  </div>
  <div class="abs info" style="left:558px">
    <svg viewBox="0 0 30 24"><path d="M2 9 15 1l13 8v13H2z" fill="var(--orange)"/><path d="M6 7h18v8l-9 5-9-5z" fill="#fff"/><path d="M2 9l13 9 13-9" fill="none" stroke="var(--orange)" stroke-width="1.5"/></svg>
    <div>Email<br>inquiry@codevanta.com</div>
  </div>

  <footer class="abs footer">Copyright @ 2016 codevanta.&nbsp; All Rights Reserved.</footer>
</div>
</body>
</html>
```